Local Flower Farm Needs Business Card Design

I need business cards designed for a flower farm based in Eudora, Kansas.
Business Info:
We are a local cut flower farm located in Eudora, Kansas, founded by Corinne Haldwick. What started as a passion for agriculture and search for more joy in daily life has blossomed into a small business dedicated to providing the community with beautiful, fresh, and sustainable flowers. We specialize in local, seasonal blooms, ensuring that every petal reflects the care and dedication we pour into our craft. Our mission is to deliver the highest quality flowers directly to our customers through local farmers markets and to florists who share our commitment to sustainability. Join us in celebrating the beauty of nature, one bloom at a time!
Contact Details:
Corinne Haldwick
Owner
Phone 913-555-0147
Facebook: Rosalind Thorpe Gardens
Instagram: @RosalindThorpeGardens
Website: RosalindThorpeGardens.example
Target Market(s)
Wholesale to Florists and Direct to Consumer via Farmers Market
Industry/Entity Type
Florist, Farm
Contact Information for Business Card
Name, Contact Info, Logo
Look and feel
Each slider illustrates characteristics of the customer's brand and the style your logo design should communicate.

```html
<!DOCTYPE html>
<html lang="en">
<head>
<meta charset="utf-8">
<title>Rosalind Thorpe Gardens – Business Card</title>
<link href="https://fonts.googleapis.com/css2?family=EB+Garamond:wght@400;500;700&display=swap" rel="stylesheet">
<style>
  :root {
    --backdrop: #e4e5e6;
    --card: #ffffff;
    --ink: #12292b;
    --stripe-grey: #c3c6c8;
    --muted: #2a2f30;
  }
  * { box-sizing: border-box; margin: 0; padding: 0; }
  html, body { width: 1200px; height: 813px; overflow: hidden; }
  body {
    background: var(--backdrop);
    font-family: "EB Garamond", Georgia, serif;
    color: var(--ink);
    position: relative;
  }
  .card {
    position: absolute;
    width: 540px;
    height: 309px;
    background: var(--card);
    border-radius: 22px;
    overflow: hidden;
    box-shadow: 0 10px 28px rgba(0,0,0,0.18);
  }
  .card--front { left: 60px; top: 110px; }
  .card--back { left: 600px; top: 394px; }

  .emblem {
    position: absolute;
    border: 1.5px solid var(--ink);
    border-radius: 50%;
    display: flex;
    align-items: center;
    justify-content: center;
    text-align: center;
    text-transform: uppercase;
    font-weight: 500;
    color: var(--ink);
  }
  .card--front .emblem {
    width: 200px; height: 200px;
    left: 170px; top: 54px;
    font-size: 22px; line-height: 1.25; letter-spacing: 2px;
  }
  .card--back .emblem {
    width: 110px; height: 110px;
    right: 22px; top: 18px;
    font-size: 12px; line-height: 1.25; letter-spacing: 1px;
  }

  .card__bands { position: absolute; left: 0; top: 0; width: 540px; height: 309px; }

  .contact-block { position: absolute; left: 28px; top: 128px; }
  .contact-block__name { font-size: 19px; font-weight: 700; line-height: 1.1; }
  .contact-block__role { font-size: 13px; color: var(--muted); margin-top: 2px; }
  .name-rule {
    position: absolute; left: 200px; right: 40px; top: 150px;
    height: 1.5px; background: var(--ink);
  }
  .contact-list { list-style: none; margin-top: 12px; }
  .contact-list li {
    display: flex; align-items: center; gap: 5px;
    font-size: 14px; line-height: 20px; color: var(--ink);
  }
  .contact-list svg { width: 11px; height: 11px; flex: none; }
  .marker { width: 10px; height: 10px; background: var(--ink); flex: none; }
  .marker--round { border-radius: 50%; }
</style>
</head>
<body>
  <section class="card card--front">
    <div class="emblem">Rosalind<br>Thorpe<br>Gardens</div>
  </section>

  <section class="card card--back">
    <svg class="card__bands" viewBox="0 0 540 309" aria-hidden="true">
      <polygon points="300,228 540,228 540,233 297,233" fill="var(--ink)"/>
      <polygon points="292,240 540,240 540,256 280,256" fill="var(--stripe-grey)"/>
      <polygon points="0,292 252,292 276,262 540,262 540,309 0,309" fill="var(--ink)"/>
    </svg>

    <div class="emblem">Rosalind<br>Thorpe<br>Gardens</div>
    <div class="name-rule"></div>

    <div class="contact-block">
      <p class="contact-block__name">Corinne Haldwick</p>
      <p class="contact-block__role">Owner</p>
      <ul class="contact-list">
        <li>
          <svg viewBox="0 0 24 24"><path fill="var(--ink)" d="M6.6 10.8a15.1 15.1 0 0 0 6.6 6.6l2.2-2.2a1 1 0 0 1 1-.25 11.4 11.4 0 0 0 3.6.57 1 1 0 0 1 1 1V20a1 1 0 0 1-1 1A17 17 0 0 1 3 4a1 1 0 0 1 1-1h3.5a1 1 0 0 1 1 1c0 1.25.2 2.45.57 3.57a1 1 0 0 1-.25 1z"/></svg>
          913-555-0147
        </li>
        <li><span class="marker marker--round"></span>RosalindThorpeGardens.example</li>
        <li><span class="marker"></span>Rosalind Thorpe Gardens</li>
        <li><span class="marker"></span>@RosalindThorpeGardens</li>
      </ul>
    </div>
  </section>
</body>
</html>
```